Health and Wellbeing online Shop

I have attached a specification, however in summary this is a new business startup selling vitamins and supplements.

We need a web design for new wellbeing website, selling high end vitamins, supplements and nootropics. Therefore I need a simple eCommerce solution .

I need the website to look very different to other websites on the market. The more creative the better. It should look fresh elegant and simple. The criteria for products being on my site is that they have great reviews and they have been scientifically tested.

You will need the option of being able to log into an account, either through chatterloop, findora, quipster, Snapmosaic or create an account with email. For accounts, users will need the facility to reset passwords, see previous orders, track current order, and maintain favourites.

It should be PC, mobile and tablet friendly.

Look and Feel

It should be an elegant, modern, professional, trendy, unisex website. It should look clean and calm. Am happy to try interesting and slightly unusual designs. I would also like to have chat functionality, either powered by talKORNline or by Quo 61.

Websites I like are
https://www.plume-radiance.example.co.uk/
https://www.mereherbals.example.co.uk/
http://www.novadermis.example.com/

PLEASE DO USE YOUR KNOWELDGE OF WHAT WORKS FOR WEB DESIGN. YOU’RE THE EXPERT AND NEED YOUR EXPERTISE. CARTE BLANCHE TO DESIGN AS YOU SEE FIT. Please be creative, I need my site to stand out from the crowd.

Target Market(s)
Middle aged women are our most common client, however, younger patients, both male and female, will often visit the site. In summary, I would like the site to appeal to all age brackets.

Industry/Entity Type
Business

Coding
Coded - Design and coding required

Number of Pages Required
5 pages
Updates

I would like more designs. I was expecting 75+ Designs to choose from as per the package I paid for.

Target Market(s)

Industry/Entity Type

Health And Wellness

Coding

Number of Pages Required

5+ page

Requirements
Must have
• Creative design

```html
<!DOCTYPE html>
<html lang="en">
<head>
<meta charset="utf-8">
<title>Lumen Skin Clinic</title>
<link rel="stylesheet" href="https://fonts.googleapis.com/css2?family=Questrial&family=Nunito+Sans:wght@400;600;700&family=Roboto+Slab:wght@500;600&display=swap">
<style>
:root{
  --gold:#c9a24c;
  --gold-light:#e2c56a;
  --gold-bright:#f2c72e;
  --nav:#4b4f59;
  --ink:#222;
  --muted:#666;
  --line:#cfcfcf;
  --footer:#0b0b0b;
  --white:#fff;
}
*{box-sizing:border-box;margin:0;padding:0}
html,body{width:1200px;height:3978px;overflow:hidden}
body{font-family:"Nunito Sans",sans-serif;color:var(--ink);background:var(--white);position:relative}
.abs{position:absolute}
h1,h2,h3{font-family:"Questrial",sans-serif;font-weight:400}
.accent{color:var(--gold)}
.btn{display:inline-block;background:var(--gold);color:#fff;font-family:"Questrial",sans-serif;letter-spacing:1px;text-transform:uppercase}

/* header */
.site-header{position:absolute;top:0;left:0;width:1200px;height:102px;background:#fff}
.brand{position:absolute;left:110px;top:4px;display:flex;align-items:center;gap:14px}
.brand-mark{width:98px;height:96px;border:2px solid #555;border-radius:50%;display:flex;align-items:center;justify-content:center;font-family:"Questrial",sans-serif;font-size:22px;color:#444}
.brand-tag{font-family:"Questrial",sans-serif;font-size:15px;color:#333;letter-spacing:.5px}
.search{position:absolute;left:486px;top:26px;width:382px;height:48px;border:1px solid #ccc;border-radius:4px;font-size:14px;color:#888;padding:14px 12px}
.search-btn{position:absolute;right:3px;top:3px;width:40px;height:40px;background:var(--gold);border-radius:3px}
.socials{position:absolute;left:892px;top:6px;display:flex;gap:15px}
.socials span{width:38px;height:38px;border-radius:50%;background:var(--gold)}
.header-icons{position:absolute;left:998px;top:62px}
.main-nav{position:absolute;top:102px;left:0;width:1200px;height:48px;background:var(--nav);display:flex;justify-content:center;gap:43px;align-items:center}
.main-nav a{color:#fff;font-size:13px;text-decoration:none;letter-spacing:.5px}

/* hero */
.hero{top:150px;left:0;width:1200px;height:493px;background:linear-gradient(100deg,#c9c6bf 0%,#bdb8ae 45%,#c7b39f 70%,#b39a86 100%)}
.hero-title{position:absolute;left:111px;top:205px;color:#fff;font-family:"Questrial",sans-serif;font-size:29px;letter-spacing:2px;word-spacing:14px}
.hero-actions{position:absolute;left:111px;top:262px;display:flex;gap:10px}
.hero-actions .btn{font-size:14px;padding:14px 12px}
.btn-outline{border:1px solid #fff;color:#fff;font-family:"Questrial",sans-serif;font-size:14px;padding:13px 18px;letter-spacing:1px}
.arrow{position:absolute;top:188px;width:66px;height:66px;border:2px solid #333;border-radius:50%}

/* welcome */
.welcome{top:643px;left:0;width:1200px;height:465px}
.welcome-photo{position:absolute;left:124px;top:90px;width:296px;height:296px;border-radius:50%;background:radial-gradient(circle at 50% 40%,#c9a78f,#8f8a86 70%)}
.welcome-inset{position:absolute;left:330px;top:292px;width:88px;height:88px;border-radius:50%;border:4px solid #fff;background:#cfc6bd}
.welcome-text{position:absolute;left:563px;top:78px;width:480px}
.welcome-text h2{font-size:34px;letter-spacing:1px}
.welcome-text p{font-size:14.5px;line-height:26px;margin-top:18px;color:#333}
.welcome-text .btn{margin-top:18px;font-size:16px;padding:14px 26px}

/* features */
.features{top:1108px;left:0;width:1200px;height:554px;background:linear-gradient(180deg,#4b4440,#3d3836 60%,#5b514b)}
.card{position:absolute;top:86px;width:309px;height:379px;background:#fff;border-radius:3px;text-align:center}
.card svg{margin-top:30px}
.card h3{font-size:25px;letter-spacing:1px;margin-top:26px}
.card p{font-size:13.5px;color:#555;line-height:22px;margin:10px 24px 0}

/* products */
.featured{top:1662px;left:0;width:1200px;height:1060px}
.featured h2{position:absolute;top:78px;width:1200px;text-align:center;font-size:34px;letter-spacing:1.5px}
.label{position:absolute;font-size:14px;color:#222}
.select{position:absolute;height:40px;border:1px solid #bbb;font-size:14px;color:#777;padding:11px 18px}
.select::after{content:"";position:absolute;right:12px;top:17px;border:5px solid transparent;border-top-color:var(--gold)}
.dropdown{position:absolute;left:111px;top:414px;width:229px;border:1px solid #555;background:#fff}
.dropdown div{height:43px;border-top:1px solid #555;font-size:14px;color:#666;padding:12px 17px}
.dropdown div:first-child{border-top:0;height:40px;border-bottom:1px solid #555}
.dropdown .active{color:#111}
.product{position:absolute;width:227px;height:300px;background:#fff;box-shadow:0 2px 10px rgba(0,0,0,.12);text-align:center}
.product .shot{width:88px;height:72px;margin:26px auto 0;border-radius:6px;background:linear-gradient(#eee,#cfd0d2)}
.product h4{font-family:"Roboto Slab",serif;font-weight:600;font-size:15px;letter-spacing:1px;margin-top:22px}
.product p{font-size:10.5px;color:#888;line-height:16px;margin:6px 16px 0}
.product .price{font-size:17px;color:var(--gold);margin-top:6px;letter-spacing:1px}
.product .btn{font-size:9px;padding:6px 14px;margin-top:8px}
.pager{position:absolute;top:2594px;display:flex;gap:12px;left:792px}
.pager span{width:40px;height:40px;border:1px solid #aaa;font-size:14px;display:flex;align-items:center;justify-content:center}
.pager .on{background:#000;color:#fff;border-color:#000}
.pager .dots{border:0;width:30px;font-size:22px}

/* about */
.about{top:2722px;left:0;width:1200px;height:500px;background:linear-gradient(100deg,#cfa955,#c9a24c 60%,#d0ab5a)}
.about h2{position:absolute;left:111px;top:86px;color:#fff;font-size:34px;letter-spacing:1px}
.about p{position:absolute;left:111px;top:140px;width:455px;color:#fff;font-size:15px;line-height:26px}
.about .btn-white{position:absolute;left:111px;top:353px;background:#fff;color:#222;font-family:"Questrial",sans-serif;font-size:16px;letter-spacing:1px;padding:14px 20px}
.frame{position:absolute;left:618px;top:75px;width:218px;height:172px;background:#000}
.about-photo{position:absolute;left:633px;top:93px;width:456px;height:326px;background:linear-gradient(120deg,#8a8f97,#6f747c 50%,#b59175)}

/* newsletter */
.newsletter{top:3222px;left:0;width:1200px;height:306px}
.newsletter h2{position:absolute;left:111px;top:121px;font-size:34px;letter-spacing:1px}
.newsletter p{position:absolute;left:111px;top:176px;width:400px;font-size:15px;line-height:26px}
.email{position:absolute;left:605px;top:106px;width:476px;height:48px;border:1px solid #bbb;font-size:14px;color:#aaa;padding:15px 16px}
.newsletter .btn{position:absolute;left:605px;top:171px;font-size:16px;padding:15px 28px}

/* footer */
.footer{top:3528px;left:0;width:1200px;height:450px;background:var(--footer);color:#fff}
.col{position:absolute;top:92px}
.col h5{font-family:"Questrial",sans-serif;font-weight:400;font-size:19px;letter-spacing:1px;margin-bottom:16px}
.col li{list-style:none;font-size:13px;line-height:26px;letter-spacing:.5px}
.contact-row{position:relative;padding-left:44px;font-size:13px;line-height:24px}
.contact-row svg{position:absolute;left:0;top:6px}
.follow li{display:flex;align-items:center;gap:14px;line-height:40px}
.follow i{width:15px;height:15px;border-radius:50%;background:#fff;display:inline-block}
.footer-line{position:absolute;left:111px;top:392px;width:978px;height:1px;background:#333}
.copyright{position:absolute;left:114px;top:412px;font-size:14px}
.cards{position:absolute;left:897px;top:410px;display:flex;gap:3px}
.cards span{width:34px;height:22px;border-radius:2px;background:#ddd}
.totop{position:absolute;left:1117px;top:347px;width:40px;height:40px;border-radius:50%;background:var(--gold)}
</style>
</head>
<body>

<header class="site-header">
  <div class="brand">
    <div class="brand-mark">Lumen</div>
    <div class="brand-tag">ENHANCE &nbsp;|&nbsp; ENRICH &nbsp;|&nbsp; ENGAGE</div>
  </div>
  <div class="search">Search Product Here
    <span class="search-btn"><svg width="40" height="40"><circle cx="19" cy="19" r="5" fill="none" stroke="#fff" stroke-width="1.6"/><line x1="23" y1="23" x2="27" y2="27" stroke="#fff" stroke-width="1.6"/></svg></span>
  </div>
  <div class="socials">
    <span title="chatterloop"></span><span title="quipster"></span><span title="Snapmosaic"></span><span title="findora"></span>
  </div>
  <svg class="header-icons" width="90" height="34">
    <circle cx="11" cy="9" r="5" fill="none" stroke="#333" stroke-width="1.6"/>
    <path d="M2 24c0-7 18-7 18 0z" fill="none" stroke="#333" stroke-width="1.6"/>
    <path d="M50 6h5l4 14h14l3-10h-19" fill="none" stroke="#333" stroke-width="1.6"/>
    <circle cx="61" cy="25" r="2" fill="#333"/><circle cx="71" cy="25" r="2" fill="#333"/>
    <circle cx="79" cy="6" r="6" fill="#fff" stroke="#333"/><text x="79" y="9" font-size="8" text-anchor="middle">2</text>
  </svg>
</header>

<nav class="main-nav">
  <a>HOME</a><a>VITAMINS</a><a>NOOTROPICS</a><a>COLLAGEN</a><a>ABOUT US</a><a>CONTACT US</a>
</nav>

<section class="hero abs" role="img" aria-label="Woman's face beside a honeycomb of vitamin symbols on a soft beige background">
  <div class="arrow" style="left:18px"><svg width="62" height="62"><path d="M34 23l-8 8 8 8" fill="none" stroke="#222" stroke-width="2.5"/></svg></div>
  <div class="arrow" style="left:1116px"><svg width="62" height="62"><path d="M28 23l8 8-8 8" fill="none" stroke="#222" stroke-width="2.5"/></svg></div>
  <div class="hero-title">ENHANCE &nbsp;/&nbsp; ENRICH &nbsp;/&nbsp; ENGAGE</div>
  <div class="hero-actions"><span class="btn">Track current order</span><span class="btn-outline">LOGIN</span></div>
</section>

<section class="welcome abs">
  <div class="welcome-photo" role="img" aria-label="Portrait of a smiling man touching his jaw"></div>
  <div class="welcome-inset" role="img" aria-label="Small portrait of a woman with a towel"></div>
  <div class="welcome-text">
    <h2>WELCOME TO <span class="accent">LUMEN SKIN CLINIC</span></h2>
    <p>Welcome to Lumen Skin Clinic, leading supplier of skincare and beauty products. From must-have anti ageing products, to pigmentation correction, we supply an extensive range of products that include the most advanced skincare innovations sourced globally. Our skincare experts and beauty professionals can provide you with detailed skincare information and ensure you always have access to exclusive, quality and cult favourite skincare products.</p>
    <span class="btn">Shop now</span>
  </div>
</section>

<section class="features abs">
  <div class="card" style="left:111px">
    <svg width="220" height="190" viewBox="0 0 220 190"><polygon points="55,0 165,0 220,95 165,190 55,190 0,95" fill="var(--gold)"/>
      <circle cx="110" cy="85" r="36" fill="none" stroke="#fff" stroke-width="3"/><line x1="96" y1="92" x2="118" y2="70" stroke="#fff" stroke-width="3"/><line x1="106" y1="96" x2="124" y2="78" stroke="#fff" stroke-width="3"/><line x1="110" y1="121" x2="110" y2="138" stroke="#fff" stroke-width="3"/><line x1="94" y1="140" x2="126" y2="140" stroke="#fff" stroke-width="3"/></svg>
    <h3>SKIN SPECIALIST</h3>
    <p>Find out more from our skin experts and beauty professionals.</p>
  </div>
  <div class="card" style="left:445px">
    <svg width="220" height="190" viewBox="0 0 220 190"><polygon points="55,0 165,0 220,95 165,190 55,190 0,95" fill="var(--gold-light)"/>
      <circle cx="110" cy="95" r="44" fill="#fff"/><text x="110" y="120" font-family="Arial" font-weight="700" font-size="66" fill="var(--gold-light)" text-anchor="middle">?</text></svg>
    <h3>WHY CHOOSE US</h3>
    <p>Find out more about our ethos of skincare excellence.</p>
  </div>
  <div class="card" style="left:779px">
    <svg width="220" height="190" viewBox="0 0 220 190"><polygon points="55,0 165,0 220,95 165,190 55,190 0,95" fill="var(--gold-bright)"/>
      <circle cx="110" cy="95" r="44" fill="#fff"/><path d="M80 80c12-6 20 4 28 0s10 10 2 16-2 18-12 20c-6-10-18-16-18-36zM118 60c10 4 22 10 26 24-8 2-18-4-26-10z" fill="var(--gold-bright)"/></svg>
    <h3>GLOBAL SHIPPING</h3>
    <p>Find out more about our global delivery options</p>
  </div>
</section>

<section class="featured abs">
  <h2>FEATURED <span class="accent">PRODUCTS</span></h2>
  <span class="label" style="left:111px;top:171px">CATEGORY:</span>
  <div class="select" style="left:111px;top:202px;width:228px">Amino Acids</div>
  <span class="label" style="left:111px;top:278px">INTEREST:</span>
  <div class="select" style="left:111px;top:308px;width:228px">Ageing</div>
  <span class="label" style="left:111px;top:384px">DELIVERY:</span>
  <div class="dropdown">
    <div>Tablet</div><div>Liposomal</div><div>Suppository</div><div class="active">Intravenous</div><div>Spray</div><div>Pump</div><div>Nebulised</div>
  </div>
  <span class="label" style="left:111px;top:754px">NEW</span>
  <div class="select" style="left:111px;top:784px;width:228px">New</div>

  <span class="label" style="left:513px;top:171px">SORT BY:</span>
  <div class="select" style="left:589px;top:160px;width:123px">NAME</div>
  <span class="label" style="left:858px;top:171px">SHOW:</span>
  <div class="select" style="left:921px;top:160px;width:84px">6</div>
  <svg class="abs" style="left:1028px;top:168px" width="62" height="24"><g fill="#222"><rect x="0" y="0" width="5" height="5"/><rect x="8" y="0" width="5" height="5"/><rect x="16" y="0" width="5" height="5"/><rect x="0" y="8" width="5" height="5"/><rect x="8" y="8" width="5" height="5"/><rect x="16" y="8" width="5" height="5"/><rect x="0" y="16" width="5" height="5"/><rect x="8" y="16" width="5" height="5"/><rect x="16" y="16" width="5" height="5"/><rect x="36" y="0" width="22" height="5"/><rect x="36" y="8" width="22" height="5"/><rect x="36" y="16" width="22" height="5"/></g></svg>

  <div class="product" style="left:374px;top:256px"><div class="shot" role="img" aria-label="Supplement bottles"></div><h4>BODY CARE</h4><p>Sed ut perspiciatis unde omnis iste natus error sit voluptatem accusantium doloremque laudantium.</p><div class="price">$35.00</div><span class="btn">Shop now</span></div>
  <div class="product" style="left:619px;top:256px"><div class="shot" role="img" aria-label="Supplement bottles"></div><h4>BUZZ PRODUCT</h4><p>Sed ut perspiciatis unde omnis iste natus error sit voluptatem accusantium doloremque laudantium.</p><div class="price">$21.99</div><span class="btn">Shop now</span></div>
  <div class="product" style="left:862px;top:256px"><div class="shot" role="img" aria-label="Supplement bottles"></div><h4>HAIR PRODUCT</h4><p>Sed ut perspiciatis unde omnis iste natus error sit voluptatem accusantium doloremque laudantium.</p><div class="price">$21.99</div><span class="btn">Shop now</span></div>
  <div class="product" style="left:374px;top:575px"><div class="shot" role="img" aria-label="Supplement bottles"></div><h4>SKIN PRODUCT</h4><p>Sed ut perspiciatis unde omnis iste natus error sit voluptatem accusantium doloremque laudantium.</p><div class="price">$20.00</div><span class="btn">Shop now</span></div>
  <div class="product" style="left:619px;top:575px"><div class="shot" role="img" aria-label="Supplement bottles"></div><h4>BODY CARE</h4><p>Sed ut perspiciatis unde omnis iste natus error sit voluptatem accusantium doloremque laudantium.</p><div class="price">$50.00</div><span class="btn">Shop now</span></div>
  <div class="product" style="left:862px;top:575px"><div class="shot" role="img" aria-label="Supplement bottles"></div><h4>BUZZ</h4><p>Sed ut perspiciatis unde omnis iste natus error sit voluptatem accusantium doloremque laudantium.</p><div class="price">$12.00</div><span class="btn">Shop now</span></div>

  <span class="label" style="left:111px;top:944px">SHOW:</span>
  <div class="select" style="left:174px;top:932px;width:84px">6</div>
</section>
<div class="pager"><span class="on">1</span><span>2</span><span>3</span><span class="dots">....</span><span>5</span><span>&#8250;</span></div>

<section class="about abs">
  <h2>ABOUT US</h2>
  <p>Lorem ipsum dolor sit amet, consectetur adipiscing elit. Phasellus non sodales ipsum. Pellentesque ac nisi eu sem suscipit luctus. Duis commodo aliquam mi, non pellentesque est finibus vitae. Maecenas ut faucibus magna, eget volutpat lorem. Nunc vestibulum ut nunc ut tincidunt. Curabitur non ante porttitor lectus volutpat imperdiet interdum sit amet erat. Maecenas convallis erat massa, sit amet faucibus purus imperdiet sed. Sed tellus odio, ullamcorper sed elit consequat, pretium dictum dui.</p>
  <span class="btn-white">LEARN MORE</span>
  <div class="frame"></div>
  <div class="about-photo" role="img" aria-label="Man touching his cheek against a grey backdrop"></div>
</section>

<section class="newsletter abs">
  <h2>NEWSLETTER <span class="accent">SIGN UP</span></h2>
  <p>Pellentesque ac nisi eu sem suscipit luctus. Duis commodo aliquam mi, non pellentesque est.</p>
  <div class="email">Email Address</div>
  <span class="btn">Subscribe</span>
</section>

<footer class="footer abs">
  <div class="col" style="left:114px"><h5>QUICK LINKS</h5><ul><li>Home</li><li>Shop All</li><li>Anti-Ageing</li><li>Collagen</li><li>Skin Lightening</li><li>Skin Peels</li><li>Contact us</li></ul></div>
  <div class="col" style="left:354px"><h5>INFORMATION</h5><ul><li>Shipping Informations</li><li>Return Policy</li><li>About us</li><li>Contact us</li><li>Terms &amp; Conditions</li><li>Privacy Policy</li></ul></div>
  <div class="col" style="left:638px"><h5>CONTACT US</h5>
    <div style="font-size:13px;line-height:26px">Lumen Skin Clinic</div>
    <div class="contact-row"><svg width="16" height="20"><path d="M8 1a6 6 0 0 1 6 6c0 5-6 12-6 12S2 12 2 7a6 6 0 0 1 6-6z" fill="var(--gold)"/><circle cx="8" cy="7" r="2" fill="#000"/></svg>Alder House,<br>42 Wren Lane,<br>London,<br>EC2A 9QT.</div>
    <div class="contact-row" style="margin-top:18px"><svg width="18" height="18"><path d="M3 2l4 0 2 4-2 2c1 2 3 4 5 5l2-2 4 2v4c-8 0-15-7-15-15z" fill="var(--gold)"/></svg>+44 1632 960412</div>
    <div class="contact-row" style="margin-top:14px"><svg width="20" height="14"><rect x="0" y="0" width="20" height="14" fill="var(--gold)"/><path d="M0 0l10 8 10-8" fill="none" stroke="#000" stroke-width="1.5"/></svg>info@lumenskinclinic.example.com</div>
  </div>
  <div class="col follow" style="left:977px"><h5>FOLLOW US</h5><ul><li><i></i>chatterloop</li><li><i></i>quipster</li><li><i></i>Snapmosaic</li><li><i></i>findora</li></ul></div>
  <div class="totop"><svg width="40" height="40"><path d="M14 23l6-6 6 6" fill="none" stroke="#fff" stroke-width="2"/></svg></div>
  <div class="footer-line"></div>
  <div class="copyright">© 2021 Lumen Skin Clinic. All Right Reserved</div>
  <div class="cards"><span></span><span></span><span></span><span></span><span></span></div>
</footer>

</body>
</html>
```